2-3 Eröffnungsplakate mit Text und Bild
Zielgruppe
Wir verkaufen Industridesign Möbel , Massivholz Tische , Lederstühle und Sitzbänke sowie Loungesessel zu Fabrikpreisen. Zielgruppe ist 25-50 , Stilorientiert und Modebewusst. Individualisten die gerne Ihr Zuhause nicht von der Stange einrichten.
Aufgabenstellung
Wir eröffnen in ca 3 Wochen einen neuen Laden mit unserer Möbel. Der Laden ist direkt an einer viel befahrenen straße. Das Plakat soll für die Neueröffnung werben und eines oder mehrere der angefügten Bilder beinhalten. Die Plakate werden Bauzaungroß also
340cm x 173cm
Es darf nicht viel Text vorkommen, sodass man beim vorbeifahren alles wichtige Lesen kann. Textbeispiele :
- NEUERÖFFNUNG. Massivholztische zu Fabrikpreisen
- NEUERÖFFNUNG. WOHNEN IM LOFT UND INDUSTRIDESIGN ZU HERSTELLERPREISEN
- NEUERÖFFNUNG. Erleben Sie Wohnen im Industrial Design. Einfach und Modern - OHNE ZWISCHENHANDEL DIREKT ZU FABRIKPREISEN
andere Textvorschläge sind erwünscht

```html
<!DOCTYPE html>
<html lang="de">
<head>
<meta charset="utf-8">
<title>Neueröffnung – Massivholztische zu Fabrikpreisen</title>
<link rel="stylesheet" href="https://fonts.googleapis.com/css2?family=Pacifico&family=Montserrat:wght@800&family=Jost:wght@400&display=swap">
<style>
  :root {
    --wall-light: #d9d6cf;
    --wall-mid: #a9a49a;
    --floor-dark: #5b4636;
    --floor-mid: #8a6d55;
    --panel-blue: rgba(38, 82, 118, 0.78);
    --accent-orange: rgba(224, 140, 40, 0.92);
    --text-white: #ffffff;
  }
  html, body {
    margin: 0;
    padding: 0;
    width: 1200px;
    height: 611px;
    overflow: hidden;
    background: #ffffff;
  }
  .poster {
    position: relative;
    width: 1200px;
    height: 611px;
    overflow: hidden;
  }
  .poster__photo {
    position: absolute;
    inset: 0;
    background:
      linear-gradient(180deg, var(--wall-light) 0%, var(--wall-mid) 52%, var(--floor-mid) 60%, var(--floor-dark) 100%);
  }
  .poster__panel {
    position: absolute;
    top: 0;
    left: 690px;
    width: 510px;
    height: 611px;
    background: var(--panel-blue);
  }
  .poster__type {
    position: absolute;
    inset: 0;
  }
  .headline-script {
    font-family: 'Pacifico', cursive;
    fill: var(--text-white);
  }
  .headline-block {
    font-family: 'Montserrat', sans-serif;
    font-weight: 800;
    fill: var(--accent-orange);
  }
  .tagline {
    font-family: 'Jost', sans-serif;
    font-weight: 400;
    fill: var(--text-white);
  }
  .rule {
    stroke: var(--text-white);
    stroke-width: 2;
  }
</style>
</head>
<body>
  <main class="poster">
    <div class="poster__photo" role="img" aria-label="Foto: Massivholztisch mit Stahlkufen, braune Lederstühle und Drehhocker in einer Loft-Halle mit Betonwand und Holzdielen"></div>
    <div class="poster__panel"></div>
    <svg class="poster__type" width="1200" height="611" viewBox="0 0 1200 611">
      <line class="rule" x1="740" y1="37" x2="1162" y2="37"/>
      <text class="headline-script" x="704" y="108" font-size="64" textLength="490" lengthAdjust="spacingAndGlyphs">Neueröffnung</text>
      <text class="headline-block" x="742" y="227" font-size="104" textLength="385" lengthAdjust="spacingAndGlyphs">MASSIV</text>
      <text class="headline-block" x="725" y="333" font-size="140" textLength="438" lengthAdjust="spacingAndGlyphs">HOLZ</text>
      <text class="headline-block" x="735" y="413" font-size="104" textLength="402" lengthAdjust="spacingAndGlyphs">TISCHE</text>
      <text class="tagline" x="736" y="522" font-size="46" textLength="426" lengthAdjust="spacingAndGlyphs">ZU FABRIKPREISEN</text>
      <line class="rule" x1="740" y1="544" x2="1162" y2="544"/>
    </svg>
  </main>
</body>
</html>
```